New Business Card Design Project

I need a design for business cards, i am an electrical business called "Corvane Electrical and Communications" i need the cards to be double sided with the company logo on the back (attached) the front needs to say my company name, web site, email address, telephone number, and ABN number and electrical license number. I am open to different arrangements of the information but would like the background to be incorporating something electrical or something that looks smart. open to all additional ideas also.

The company colours are orange and grey see logo attached.

Business Name: Corvane Electrical and Communications
Website: corvaneelectricalandcomms.example.com.au
Email: brent@corvaneelectricalandcomms.example.com.au
Telephone(mobile): 0481209736
ABN: 71208349162
Lic No: 418273D

Target Market(s)

Business entities, Project Managers, Accounts, Clients

Industry/Entity Type

Electrician

Contact Information for Business Card

I need a design for business cards, i am an electrical business called "Corvane Electrical and Communications" i need the cards to be double sided with the company logo on the back (attached) the front needs to say my company name

Font styles to use
Serif
Sans Serif

Colors
f37122
5c5c5c

Requirements
Must have
• Must have the Logo on the back open to different ways of it being on the back but had in mind to keep it central but again open to other options
Nice to have
• A real modern cool background that is eye catching yet contemporary
Should not have
• No backgrounds of a light bulb or plug or anything like that

```html
<!DOCTYPE html>
<html lang="en">
<head>
<meta charset="utf-8">
<title>Corvane Electrical and Communications – Business Cards</title>
<link href="https://fonts.googleapis.com/css2?family=Open+Sans:wght@400;600;700&display=swap" rel="stylesheet">
<style>
  :root {
    --canvas-bg: #e9e6e2;
    --card-bg: #1f2a33;
    --text-light: #ffffff;
    --brand-yellow: #f5d10f;
    --shadow: rgba(0, 0, 0, 0.28);
  }
  * { margin: 0; padding: 0; box-sizing: border-box; }
  html, body {
    width: 1200px;
    height: 900px;
    overflow: hidden;
    background: var(--canvas-bg);
    font-family: "Open Sans", Arial, sans-serif;
  }
  .canvas {
    position: relative;
    width: 1200px;
    height: 900px;
  }
  .card {
    position: absolute;
    background: var(--card-bg);
    color: var(--text-light);
    box-shadow: 0 10px 28px var(--shadow);
    text-align: center;
  }
  .card--front {
    left: 238px; top: 62px;
    width: 555px; height: 343px;
  }
  .card--back {
    left: 457px; top: 518px;
    width: 560px; height: 344px;
    display: flex;
    align-items: center;
    justify-content: center;
  }
  .brand {
    display: flex;
    align-items: center;
    justify-content: center;
    gap: 10px;
    color: var(--text-light);
    font-weight: 600;
    line-height: 1.1;
  }
  .brand__dot {
    flex: none;
    border-radius: 50%;
    background: var(--brand-yellow);
  }
  .brand__name { text-align: left; }
  .card--front .brand {
    position: absolute;
    left: 0; right: 0; top: 58px;
    font-size: 24px;
  }
  .card--front .brand__dot { width: 16px; height: 16px; }
  .card--back .brand { font-size: 34px; margin-top: 8px; }
  .card--back .brand__dot { width: 22px; height: 22px; }
  .brand__name small {
    display: block;
    font-size: 0.5em;
    letter-spacing: 0.06em;
    text-transform: uppercase;
  }
  .holder {
    position: absolute;
    left: 0; right: 0; top: 144px;
  }
  .holder__name {
    font-size: 18px;
    font-weight: 600;
    letter-spacing: 0.02em;
    text-transform: uppercase;
    line-height: 24px;
  }
  .holder__role { font-size: 14px; line-height: 20px; }
  .registration {
    position: absolute;
    left: 0; right: 0; top: 200px;
    font-size: 14px;
    line-height: 21px;
  }
  .registration strong { font-weight: 700; }
  .contact {
    position: absolute;
    left: 0; right: 0; top: 253px;
    list-style: none;
    font-size: 14px;
    line-height: 20px;
  }
  .contact li {
    display: flex;
    align-items: center;
    justify-content: center;
    gap: 7px;
  }
  .contact svg { width: 11px; height: 11px; fill: var(--text-light); }
</style>
</head>
<body>
<main class="canvas">

  <section class="card card--front" aria-label="Business card front">
    <div class="brand">
      <span class="brand__dot"></span>
      <span class="brand__name">CORVANE<small>Electrical &amp; Communications</small></span>
    </div>

    <div class="holder">
      <p class="holder__name">Daniel Reeve</p>
      <p class="holder__role">Director</p>
    </div>

    <div class="registration">
      <p><strong>ABN:</strong> 71208349162</p>
      <p><strong>Lic No:</strong> 418273D</p>
    </div>

    <ul class="contact">
      <li>
        <svg viewBox="0 0 24 24" aria-hidden="true"><path d="M6.6 10.8a15.1 15.1 0 0 0 6.6 6.6l2.2-2.2c.3-.3.7-.4 1-.2 1.1.4 2.3.6 3.6.6.6 0 1 .4 1 1V20c0 .6-.4 1-1 1C10.6 21 3 13.4 3 4c0-.6.4-1 1-1h3.5c.6 0 1 .4 1 1 0 1.3.2 2.5.6 3.6.1.3 0 .7-.2 1z"/></svg>
        <span>0481209736</span>
      </li>
      <li>
        <svg viewBox="0 0 24 24" aria-hidden="true"><path d="M2 5h20v14H2z M4 7v.5l8 5 8-5V7l-8 5z" fill-rule="evenodd"/></svg>
        <span>brent@corvaneelectricalandcomms.example.com.au</span>
      </li>
      <li>
        <svg viewBox="0 0 24 24" aria-hidden="true"><path d="M12 2a10 10 0 1 0 0 20 10 10 0 0 0 0-20zm-1 17.9A8 8 0 0 1 4.1 10L9 15v1a2 2 0 0 0 2 2zm6.9-2.5A2 2 0 0 0 16 16h-1v-3a1 1 0 0 0-1-1H8v-2h2a1 1 0 0 0 1-1V7h2a2 2 0 0 0 2-2v-.4a8 8 0 0 1 2.9 12.8z"/></svg>
        <span>corvaneelectricalandcomms.example.com.au</span>
      </li>
    </ul>
  </section>

  <section class="card card--back" aria-label="Business card back">
    <div class="brand">
      <span class="brand__dot"></span>
      <span class="brand__name">CORVANE<small>Electrical &amp; Communications</small></span>
    </div>
  </section>

</main>
</body>
</html>
```